Business card design for a dynamic IT consulting company

We need a business card design for a young firm, specialized in the Telecommunications/Consulting industry. The name of the company is Quindor and Partners Business Consulting Ltd. (Short name: Quindor and Partnes)
Quindor = solve read reverse, so we aim to be uncomplicated and solution-oriented. The small pipe in our logo is also related to the word solve. So we need a new business card design, which is simple, eye catching and something non traditional (I would probably prefer a square shaped design rather than a rectangle, but open for suggestions). Attached our logo.

Target Market(s)

Usually our customers are Tier1 Telecoms providers (Q-Netra, Palorix, etc) and their executives.

Industry/Entity Type

Business

Contact Information for Business Card

Name: Bence Tolnavari
Email: b.tolnavari@quindor.hu
Web: www.quindor.hu
Mobile: +36 30 518 2769
Title: Managing Director

Optional:
Company name: Quindor and Partners Ltd.
Address: 1087 Budapest, Tolvenka str. 28/C, Hungary

Font styles to use
Other font styles liked:
• helveticaneue_medium, Prime Regular are used now.

Colors

Designer to choose colors to be used in the design.

Requirements
Must have
• I would like to have a 2 sided design.
Nice to have
• I thought if we make the logo a bit bigger (without the company name), that could go to the back with the company name below. I though, if the pipe in the logo is somehow touchable on the business card, would be nice and unique.

```html
<!DOCTYPE html>
<html lang="en">
<head>
<meta charset="utf-8">
<title>Quindor and Partners – Business Card</title>
<link href="https://fonts.googleapis.com/css2?family=Roboto:wght@300;400;500&display=swap" rel="stylesheet">
<style>
  :root {
    --stage: #bdbdbd;
    --card: #ffffff;
    --card-shade: #eeeeee;
    --ink-dark: #2a2a2a;
    --ink-text: #4a4a4a;
    --accent-blue: #1b9ad6;
    --accent-magenta: #c2309e;
    --accent-grey: #6e6e6e;
    --rule: #b5b5b5;
  }
  * { box-sizing: border-box; margin: 0; padding: 0; }
  html, body { width: 1200px; height: 900px; overflow: hidden; }
  body {
    background: radial-gradient(circle at 50% 40%, #d4d4d4, var(--stage));
    font-family: "Roboto", Arial, sans-serif;
    position: relative;
  }
  .card {
    position: absolute;
    left: 320px;
    width: 560px;
    height: 320px;
    border-radius: 16px;
    overflow: hidden;
    background: linear-gradient(160deg, var(--card) 40%, var(--card-shade));
    box-shadow: 0 12px 30px rgba(0,0,0,.25);
  }

  /* Card back: brand side */
  .card-brand { top: 90px; display: flex; flex-direction: column; }
  .brand-area {
    flex: 1;
    display: flex; align-items: center; justify-content: center; gap: 14px;
  }
  .brand-square { width: 26px; height: 26px; background: var(--accent-blue); }
  .brand-name {
    font-weight: 300; font-size: 44px; color: var(--accent-grey);
    letter-spacing: .5px;
  }
  .tricolour { display: flex; height: 5px; margin-bottom: 4px; }
  .tricolour .blue { flex: 40; background: var(--accent-blue); }
  .tricolour .magenta { flex: 36; background: var(--accent-magenta); }
  .tricolour .grey { flex: 24; background: var(--accent-grey); }
  .brand-band {
    height: 66px; background: var(--ink-dark);
    display: flex; align-items: center; justify-content: center;
    color: #e6e6e6; font-size: 16px; letter-spacing: .3px;
  }

  /* Card front: contact side */
  .card-contact { top: 490px; display: flex; }
  .side-band {
    width: 104px; flex: none; background: var(--ink-dark);
    display: flex; align-items: center; justify-content: center;
  }
  .side-brand {
    transform: rotate(-90deg); white-space: nowrap;
    display: flex; align-items: center; gap: 10px;
  }
  .side-brand .brand-square { width: 14px; height: 14px; }
  .side-brand .brand-name { font-size: 28px; color: #d8d8d8; }
  .tricolour-vertical { display: flex; flex-direction: column; width: 5px; flex: none; margin-left: 4px; }
  .tricolour-vertical .blue { flex: 30; background: var(--accent-blue); }
  .tricolour-vertical .magenta { flex: 30; background: var(--accent-magenta); }
  .tricolour-vertical .grey { flex: 40; background: var(--accent-grey); }
  .contact-body { flex: 1; min-width: 0; padding: 48px 22px 0 26px; position: relative; }
  .person-name { font-size: 31px; font-weight: 400; line-height: 1; }
  .person-name .first { color: var(--accent-blue); font-weight: 500; }
  .person-name .last { color: var(--accent-magenta); }
  .person-title { color: var(--ink-text); font-size: 17px; margin-top: 6px; }
  .divider { position: absolute; left: 190px; right: 22px; top: 116px; height: 1px; background: var(--rule); }
  .company { margin-top: 74px; }
  .company-name { color: var(--accent-blue); font-size: 15px; font-weight: 500; }
  .company-address { color: var(--ink-text); font-size: 15px; margin-top: 3px; }
  .contact-row { display: flex; justify-content: space-between; margin-top: 14px; font-size: 12.5px; color: var(--ink-text); }
  .contact-item { display: flex; align-items: center; gap: 6px; white-space: nowrap; }
  .icon { width: 16px; height: 16px; border-radius: 3px; display: block; flex: none; }
</style>
</head>
<body>

<section class="card card-brand" aria-label="Card back">
  <div class="brand-area">
    <span class="brand-square"></span>
    <span class="brand-name">Quindor &amp; Partners</span>
  </div>
  <div class="tricolour"><span class="blue"></span><span class="magenta"></span><span class="grey"></span></div>
  <div class="brand-band">www.quindor.hu</div>
</section>

<section class="card card-contact" aria-label="Card front">
  <div class="side-band">
    <div class="side-brand">
      <span class="brand-square"></span>
      <span class="brand-name">Quindor &amp; Partners</span>
    </div>
  </div>
  <div class="tricolour-vertical"><span class="blue"></span><span class="magenta"></span><span class="grey"></span></div>
  <div class="contact-body">
    <h1 class="person-name"><span class="first">Bence</span> <span class="last">Tolnavari</span></h1>
    <p class="person-title">Managing Director</p>
    <div class="divider"></div>
    <div class="company">
      <p class="company-name">Quindor and Partners Ltd</p>
      <p class="company-address">1087 Budapest, Tolvenka str. 28/C, Hungary</p>
    </div>
    <div class="contact-row">
      <span class="contact-item">
        <svg class="icon" viewBox="0 0 18 18"><rect width="18" height="18" rx="3" fill="#1b9ad6"/><path d="M5 4.5l2 0 1 2.5-1.3 1a6 6 0 0 0 3 3l1-1.3 2.5 1v2a1 1 0 0 1-1 1A8.5 8.5 0 0 1 4 5.5a1 1 0 0 1 1-1z" fill="#fff"/></svg>
        802.417.3390
      </span>
      <span class="contact-item">
        <svg class="icon" viewBox="0 0 18 18"><rect width="18" height="18" rx="3" fill="#c2309e"/><rect x="4" y="5.5" width="10" height="7" fill="none" stroke="#fff" stroke-width="1.2"/><path d="M4 5.5l5 4 5-4" fill="none" stroke="#fff" stroke-width="1.2"/></svg>
        b.tolnavari@quindor.hu
      </span>
      <span class="contact-item">
        <svg class="icon" viewBox="0 0 18 18"><rect width="18" height="18" rx="3" fill="#3a3a3a"/><circle cx="9" cy="9" r="5" fill="none" stroke="#fff" stroke-width="1.2"/><path d="M4 9h10M9 4c-2.5 3-2.5 7 0 10M9 4c2.5 3 2.5 7 0 10" fill="none" stroke="#fff" stroke-width="1"/></svg>
        www.quindor.hu
      </span>
    </div>
  </div>
</section>

</body>
</html>
```